Business cards and stationary design

We just completed the design of our new logo and we need to print new business cards and letterhead for our nonprofit. We are looking for a fresh new design that shows off our new logo. On letterhead, we must have a column on the right or left to include our Board of Directors (up to 45 names) (see attachment)

Industry/Entity Type

Non-Profit

Contact Information for Business Card

Standard business card with name, title, Company name, mailing address phone numbers, email address and website. Tagline on back "Bringing the homeless home"

Font styles to use
Sans Serif

Requirements
Must have
• include pertinent information above
• new logo
• fonts compatible with logo
• should use logo colors only
Nice to have
• tag lines

```html
<!DOCTYPE html>
<html lang="en">
<head>
<meta charset="utf-8">
<title>Homeward Relief Center – Letterhead</title>
<link href="https://fonts.googleapis.com/css2?family=Questrial&family=Roboto:wght@400;500;700&display=swap" rel="stylesheet">
<style>
  :root {
    --bg: #e4e4e4;
    --paper: #f2f2f2;
    --ink: #3a3a3a;
    --ink-soft: #555555;
    --teal: #1a8fb0;
    --yellow: #f5b820;
    --rule: #8a8a8a;
    --sig: #2a63b3;
  }
  html, body {
    margin: 0;
    width: 1024px;
    height: 1200px;
    overflow: hidden;
    background: var(--bg);
  }
  .letterhead {
    position: absolute;
    left: 102px;
    top: 26px;
    width: 820px;
    height: 1147px;
    background: var(--paper);
    color: var(--ink);
  }
  .brand {
    position: absolute;
    left: 80px;
    top: 106px;
    width: 230px;
    display: flex;
    align-items: center;
    gap: 10px;
  }
  .brand-mark {
    flex: none;
    width: 16px;
    height: 16px;
    background: var(--yellow);
  }
  .brand-name {
    font-family: "Roboto", sans-serif;
    font-weight: 500;
    font-size: 16px;
    line-height: 20px;
    letter-spacing: 1.5px;
    color: var(--teal);
    text-transform: uppercase;
  }
  .brand-name span { display: block; }
  .contact {
    position: absolute;
    left: 355px;
    top: 78px;
    font-family: "Roboto", sans-serif;
    font-style: normal;
    font-size: 12px;
    line-height: 13.5px;
    color: var(--ink);
  }
  .contact p { margin: 0; }
  .contact .gap { margin-top: 7px; }
  .board {
    position: absolute;
    left: 84px;
    top: 273px;
    font-family: "Roboto", sans-serif;
    font-size: 12px;
    line-height: 16.2px;
    color: var(--ink);
  }
  .board h2 {
    font-size: 12px;
    font-weight: 700;
    margin: 0 0 16px;
  }
  .board ul { list-style: none; margin: 0; padding: 0; }
  .board .officers { margin-bottom: 16px; }
  .board .officers strong { font-weight: 700; }
  .divider {
    position: absolute;
    left: 280px;
    top: 273px;
    width: 1px;
    height: 699px;
    background: var(--rule);
  }
  .letter {
    position: absolute;
    left: 355px;
    top: 276px;
    width: 392px;
    font-family: "Questrial", sans-serif;
    color: var(--ink-soft);
  }
  .salutation {
    font-size: 22px;
    margin: 0 0 28px;
    color: var(--ink);
  }
  .letter p.body {
    font-size: 13px;
    line-height: 16.5px;
    text-align: justify;
    margin: 0 0 16px;
    hyphens: auto;
  }
  .closing {
    font-size: 12.5px;
    margin: 40px 0 6px;
  }
  .signature {
    width: 130px;
    height: 56px;
    border-radius: 6px;
    background: linear-gradient(90deg, rgba(42,99,179,0.22), rgba(42,99,179,0.08));
  }
</style>
</head>
<body>
  <main class="letterhead">
    <div class="brand">
      <span class="brand-mark"></span>
      <span class="brand-name"><span>Homeward Relief</span><span>Center</span></span>
    </div>

    <address class="contact">
      <p>HOMEWARD RELIEF CENTER</p>
      <p>412 Birchwood Road</p>
      <p>Fairbanks, Alaska 99701</p>
      <p class="gap">555 210 4836</p>
      <p>paul@homewardrelief.org</p>
      <p>www.homewardrelief.org</p>
    </address>

    <aside class="board">
      <h2>Board of Directors:</h2>
      <ul class="officers">
        <li><strong>Owen Marlow</strong>,Chair</li>
        <li><strong>Neil Foster</strong>,Vice Chair</li>
        <li><strong>Tess Lindqvist</strong>,Treasurer</li>
        <li><strong>June Parrish</strong>, Secretary</li>
      </ul>
      <ul class="members">
        <li>Ross Abner</li><li>Glen Barker</li><li>Ted Bramwell</li><li>Clara Brody</li>
        <li>Max Burnett</li><li>Luke Calder</li><li>Rosalind Crane</li><li>Dean Cutler</li>
        <li>Nora Dale</li><li>Marian Garrick</li><li>Priya Gorwin</li><li>Lily Grant</li>
        <li>Brent Halloway</li><li>Sean Halloway</li><li>Vanessa Hartley</li><li>Wade Hollis</li>
        <li>Carl Hopper</li><li>Rita Hume</li><li>Stacy Irwin</li><li>Leanne Jarvis</li>
        <li>Andrea Lowell</li><li>Serena Morrow</li><li>Frank Nettleton</li><li>Mark Pavlenko</li>
        <li>Alan Pettigrew</li><li>Heather Sandoval</li><li>Grant Sokolow</li><li>Mina Sterling</li>
        <li>Wendy Stroud</li><li>Ivy Marsh</li><li>Monica Thorne</li><li>Yasmin Valdane</li>
        <li>Eileen Walsh</li><li>Kurt Winslow</li><li>Hazel Yoder</li><li>Peter Zimmerly</li>
      </ul>
    </aside>

    <div class="divider"></div>

    <article class="letter">
      <p class="salutation">Dear Mr. Carter,</p>
      <p class="body">Lorem ipsum dolor sit amet, consectetur adipiscing elit. Donec orci purus, luctus vitae dignissim eu, iaculis sed purus. Vivamus faucibus, ipsum nec aliquet viverra, leo mauris condimentum ligula, sit amet sagittis enim ligula quis arcu. Nam egestas tortor id nisi porttitor mattis. In tortor ante, ultricies in suscipit a, tempus non massa. Vivamus et auctor mi. Fusce vel massa nulla. Phasellus nec eros mauris, et scelerisque orci.</p>
      <p class="body">Donec malesuada orci vitae nulla accumsan porta a id massa. Quisque accumsan iaculis magna sit amet fringilla. Maecenas consequat, magna eget tincidunt semper, odio nibh rutrum mi, id feugiat ante nisi eu risus. Vestibulum nunc orci, rhoncus a placerat in, ultricies in mi. Cras mattis varius eros, vel fringilla nisi suscipit eget. Quisque scelerisque sagittis nulla at porttitor.</p>
      <p class="body">Sed id augue vitae urna euismod commodo aliquet a quam. Pellentesque arcu velit, cursus et malesuada ut, consequat et diam. Nullam erat sem, rhoncus id ullamcorper vitae, rhoncus et arcu. In ultricies ultricies nulla, ut rutrum nisi iaculis at. Donec eu magna a metus ornare faucibus. Fusce aliquet faucibus ultricies. Morbi semper, est id tincidunt gravida, sem arcu adipiscing lacus, ac bibendum nulla leo eu purus. Quisque nec diam sed risus consectetur a ccumsan quis quis nibh. Vestibulum id purus lorem.</p>
      <p class="body">It is a long established fact that a reader will be distracted by the readable content of a page when looking at its layout. The point of using Lorem Ipsum is that it has a more-or-less normal distribution of letters, as opposed to using 'Content here, content here', making it look like readable English. Many desktop publishing packages</p>
      <p class="closing">Sincerely,</p>
      <div class="signature" role="img" aria-label="Handwritten signature of Paul Reyes"></div>
    </article>
  </main>
</body>
</html>
```